Pyschiatry Experts need Marketing Campaign

Ad(s) developed for print advertising sharing our purpose and services, highlighting our medical care providers. Must be welcoming and inviting while displaying a high level of professionalism expected from a physician's office.

Target Market(s)

Local community

Industry/Entity Type

Psychiatry (Healthcare)

Requirements
Must have
• Staff pictures, 'Medication Management Experts', 'Prompt Appointments', 'ADD/ADHD, Bipolar Disorder, Depression, Anxiety, Schizophrenia, Grief Reaction and others' 'Virtual and In-Person Visits'
Nice to have
• Address: 412 E Marlowe Coeur d'Alene Phone (208)555-7193 website: BrightLoftCare.com Hours: Mon - Thur 7am - 6pm

```html
<!DOCTYPE html>
<html lang="en">
<head>
<meta charset="utf-8">
<title>Bright Loft Care – Mental Health Evaluations</title>
<link href="https://fonts.googleapis.com/css2?family=Lora:wght@700&family=Poppins:wght@400;500;600;700&family=Oswald:wght@300;500&display=swap" rel="stylesheet">
<style>
  :root{
    --page:#c8c8c8;
    --paper:#f8f7f1;
    --forest:#0c3a22;
    --teal:#12b39b;
    --sea:#0f9283;
    --deep:#0a3a1f;
    --lime:#a6df55;
    --lime-soft:rgba(166,223,85,0.55);
    --lime-dark:#6ab02f;
    --ink:#1d2a22;
    --rule:#dfe3dc;
  }
  *{margin:0;padding:0;box-sizing:border-box}
  html,body{width:1200px;height:908px;overflow:hidden;background:var(--page)}
  .flyer{
    position:absolute;left:268px;top:24px;width:979px;height:1266px;
    transform:scale(0.679);transform-origin:top left;
    background:var(--paper);overflow:hidden;
    font-family:"Poppins",sans-serif;color:var(--ink);
  }
  .abs{position:absolute}
  .headline{left:76px;top:62px;font-family:"Lora",serif;font-weight:700;font-size:65px;line-height:60px;color:var(--forest)}
  .headline .accent{color:var(--teal)}
  .divider{left:603px;top:70px;width:2px;height:168px;background:var(--rule)}
  .brand{left:640px;top:76px;width:278px;text-align:center}
  .brand-dot{width:86px;height:86px;border-radius:50%;background:var(--teal);margin:0 auto 18px}
  .brand-name{font-family:"Poppins",sans-serif;font-weight:500;font-size:29px;letter-spacing:1px;color:var(--teal);white-space:nowrap}
  .intro{left:78px;top:292px;font-size:31px;line-height:36px;color:var(--forest)}
  .intro strong{font-weight:700}
  .dots{left:80px;top:374px;display:flex;gap:5px}
  .dots span{width:8px;height:8px;border-radius:50%;background:var(--lime)}
  .dots span:nth-child(n+3){background:#cfeeb0}
  .conditions{left:78px;top:395px;list-style:none;width:282px}
  .conditions li{display:flex;align-items:center;height:52px;font-size:22px;border-bottom:2px solid var(--rule)}
  .conditions li:last-child{border-bottom:none;width:360px}
  .conditions svg{width:32px;height:32px;margin-right:24px;flex:none}
  .photo-main{left:78px;top:712px;width:352px;height:381px;border-radius:160px 160px 0 0;
    background:linear-gradient(180deg,#eac9a8 0%,#f4a98a 55%,#2c2c2c 100%)}
  .visits-band{left:0;top:1093px;width:490px;height:34px;background:var(--lime);border-radius:0 6px 6px 0;
    font-weight:700;font-size:20px;letter-spacing:2.6px;color:var(--forest);padding-left:74px;line-height:35px}
  .hours{left:73px;top:1140px;font-size:16px}
  .hours .label{color:var(--lime-dark);font-weight:600}
  .hours .bar{color:var(--teal)}
  .hours b{font-weight:700;color:var(--forest)}
  .site{left:73px;top:1174px;font-size:25px;font-weight:600;letter-spacing:3.6px;color:var(--ink)}
  .site .accent{color:var(--teal)}
  .care-circle{left:492px;top:308px;width:736px;height:736px;border-radius:50%;background:var(--sea)}
  .leaf-area{left:740px;top:262px;width:300px;height:230px;border-radius:50%;
    background:radial-gradient(ellipse at 60% 45%,var(--lime-soft) 0%,rgba(166,223,85,0.25) 45%,rgba(166,223,85,0) 72%)}
  .expert-ring{left:681px;top:504px;width:354px;height:354px;border-radius:50%;border:3px solid var(--lime)}
  .expert-core{left:695px;top:518px;width:326px;height:326px;border-radius:50%;background:var(--deep)}
  .expert-text{right:59px;top:622px;text-align:right;font-family:"Oswald",sans-serif;font-size:42px;line-height:40px;color:#fff;text-transform:uppercase}
  .expert-text .bold{font-weight:500}
  .expert-text .light{font-weight:300}
  .expert-text .accent{color:var(--lime);font-weight:500}
  .provider-photo{width:134px;height:134px;border-radius:50%;border:5px solid var(--lime);
    background:radial-gradient(circle at 50% 40%,#8b949a 0%,#3f474d 70%);box-shadow:0 0 0 3px var(--sea)}
  .provider{color:#fff;font-weight:700;font-size:19px;line-height:21px}
  .cred{display:inline-block;margin-top:4px;background:var(--lime);color:var(--forest);font-size:9px;font-weight:600;
    border-radius:8px;padding:0 12px;line-height:13px}
  .prompt{right:61px;top:1086px;font-family:"Lora",serif;font-weight:700;font-size:34px;color:var(--forest)}
  .prompt .accent{color:var(--teal)}
  .contact{right:61px;top:1158px;text-align:right;font-size:19px;line-height:28px}
  .contact svg{width:14px;height:14px;vertical-align:-1px;margin-right:4px}
</style>
</head>
<body>
<main class="flyer">
  <h1 class="abs headline">Comprehensive<br>Mental Health<br><span class="accent">Evaluations</span></h1>
  <div class="abs divider"></div>
  <div class="abs brand">
    <div class="brand-dot"></div>
    <div class="brand-name">BRIGHT LOFT CARE</div>
  </div>

  <p class="abs intro">Experts in the entire<br><strong>Mental Health Spectrum</strong></p>
  <div class="abs dots"><span></span><span></span><span></span><span></span></div>

  <ul class="abs conditions">
    <li><svg viewBox="0 0 32 32"><circle cx="16" cy="14" r="11" fill="var(--lime)"/><circle cx="16" cy="14" r="5" fill="var(--teal)"/></svg>ADD/ADHD</li>
    <li><svg viewBox="0 0 32 32"><circle cx="10" cy="16" r="9" fill="var(--lime)"/><circle cx="22" cy="16" r="9" fill="var(--teal)"/></svg>Bipolar Disorder</li>
    <li><svg viewBox="0 0 32 32"><circle cx="18" cy="5" r="4" fill="var(--lime)"/><rect x="11" y="12" width="10" height="18" rx="2" fill="var(--teal)"/></svg>Depression</li>
    <li><svg viewBox="0 0 32 32"><circle cx="16" cy="10" r="6" fill="var(--teal)"/><path d="M4 18h24l-5 12H9z" fill="var(--lime)"/></svg>Anxiety</li>
    <li><svg viewBox="0 0 32 32"><circle cx="16" cy="14" r="11" fill="var(--lime)"/><circle cx="16" cy="12" r="5" fill="var(--teal)"/></svg>Schizophrenia</li>
    <li><svg viewBox="0 0 32 32"><circle cx="20" cy="6" r="4" fill="var(--lime)"/><rect x="6" y="14" width="14" height="16" rx="2" fill="var(--teal)"/></svg>Grief Reaction &amp; others</li>
  </ul>

  <div class="abs photo-main" role="img" aria-label="Woman meditating cross-legged with hands pressed together"></div>
  <div class="abs visits-band">VIRTUAL AND IN-PERSON VISITS</div>
  <p class="abs hours"><span class="label">Hours:</span> Mon - Thur <span class="bar">|</span> <b>7am - 6pm</b></p>
  <p class="abs site">www.<span class="accent">brightloftcare</span>.com</p>

  <div class="abs care-circle"></div>
  <div class="abs leaf-area" role="img" aria-label="Soft green leaf decoration"></div>
  <div class="abs expert-ring"></div>
  <div class="abs expert-core"></div>
  <p class="abs expert-text"><span class="bold">Medication</span><br><span class="light">Management</span><br><span class="accent">Experts</span></p>

  <div class="abs provider-photo" style="left:555px;top:328px" role="img" aria-label="Portrait of provider Mark Delaney"></div>
  <div class="abs provider" style="left:705px;top:377px">Mark Delaney<br><span class="cred">PMHNP-BC</span></div>

  <div class="abs provider-photo" style="left:426px;top:517px" role="img" aria-label="Portrait of provider Sharon Whitley"></div>
  <div class="abs provider" style="left:580px;top:557px">Sharon<br>Whitley<br><span class="cred">PMHNP-BC</span></div>

  <div class="abs provider-photo" style="left:426px;top:735px" role="img" aria-label="Portrait of provider Tom Ashford"></div>
  <div class="abs provider" style="left:575px;top:782px">Tom Ashford<br><span class="cred">PMHNP-BC</span></div>

  <div class="abs provider-photo" style="left:555px;top:903px" role="img" aria-label="Portrait of provider Helen Marsh"></div>
  <div class="abs provider" style="left:708px;top:941px">Helen Marsh<br><span class="cred">PMHNP-BC, DNP</span></div>

  <p class="abs prompt">Prompt <span class="accent">Appointments</span></p>
  <div class="abs contact">
    <div><svg viewBox="0 0 16 16"><path d="M3 1l3 3-2 2c1 2 4 5 6 6l2-2 3 3-2 2C7 15 1 9 1 3z" fill="var(--lime-dark)"/></svg>(208)555-7193</div>
    <div><svg viewBox="0 0 16 16"><path d="M8 1a5 5 0 0 1 5 5c0 4-5 9-5 9S3 10 3 6a5 5 0 0 1 5-5z" fill="var(--lime-dark)"/><circle cx="8" cy="6" r="2" fill="var(--paper)"/></svg>412 E Marlowe Coeur d'Alene</div>
  </div>
</main>
</body>
</html>
```